Business card for law firm

Need business card for new law firm. Think confident, authoritative, conservative, but not stuffy or old-fashioned.

Contact Information for Business Card

Content for card - logo (uploaded), plus the following:

Paul Whitcombe (larger font)
Managing Partner (larger font, but not as large as name)
Level 9, 7 Ferris Lane
Sydney NSW 2000
Main Tel 02 9364 2710
Direct Tel 02 8472 3159
Email paul@qvlegal.com.au
www.qvlegal.com.au

Letterhead design should include logo plus:
Level 9, 7 Ferris Lane
Sydney NSW 2000
Tel 02 8472 3159
www.qvlegal.com.au

```html
<!DOCTYPE html>
<html lang="en">
<head>
<meta charset="utf-8">
<title>Quayvale Lawyers — Letterhead</title>
<link rel="stylesheet" href="https://fonts.googleapis.com/css2?family=Questrial&family=Roboto:wght@400&display=swap">
<style>
  :root {
    --backdrop: #e6e6e7;
    --paper: #f2f2f3;
    --paper-edge: #dedee0;
    --ink-body: #6f6f72;
    --ink-heading: #7c7c80;
    --ink-brand: #3b3b3f;
    --navy: #1d2b6e;
    --signature-blue: #c9d4ec;
  }
  * { box-sizing: border-box; margin: 0; padding: 0; }
  html, body {
    width: 1024px;
    height: 1200px;
    overflow: hidden;
    background: var(--backdrop);
  }
  .letterhead {
    position: absolute;
    left: 112px;
    top: 40px;
    width: 800px;
    height: 1120px;
    background: linear-gradient(100deg, #f6f6f7 0%, var(--paper) 55%, #e9e9eb 100%);
    border: 1px solid var(--paper-edge);
    font-family: "Questrial", "Century Gothic", sans-serif;
    color: var(--ink-body);
  }
  .brand {
    position: absolute;
    top: 66px;
    left: 0;
    width: 100%;
    text-align: center;
  }
  .brand-mark {
    display: block;
    width: 34px;
    height: 34px;
    margin: 0 auto 18px;
    background: var(--navy);
  }
  .brand-name {
    font-size: 24px;
    letter-spacing: 1.5px;
    color: var(--ink-brand);
    line-height: 1;
  }
  .letter {
    position: absolute;
    left: 74px;
    right: 66px;
    top: 296px;
  }
  .salutation {
    font-size: 19px;
    color: var(--ink-heading);
    margin-bottom: 34px;
  }
  .letter p {
    font-size: 11.4px;
    line-height: 14.4px;
    text-align: justify;
    margin-bottom: 14.4px;
  }
  .sign-off {
    margin-top: 30px;
    font-size: 11.4px;
  }
  .signature {
    display: block;
    margin-top: 44px;
    width: 170px;
    height: 64px;
    background: linear-gradient(90deg, var(--signature-blue), #e3e8f4);
    border-radius: 4px;
  }
  .footer {
    position: absolute;
    left: 74px;
    right: 66px;
    top: 1024px;
    border-top: 1px solid var(--navy);
    padding-top: 19px;
    text-align: center;
    font-family: "Roboto", Arial, sans-serif;
    font-size: 14px;
    line-height: 18px;
    color: var(--navy);
  }
</style>
</head>
<body>
  <main class="letterhead">
    <header class="brand">
      <span class="brand-mark"></span>
      <div class="brand-name">QUAYVALE LAWYERS</div>
    </header>

    <section class="letter">
      <h1 class="salutation" style="font-weight:400">Dear Mr. Hartley,</h1>
      <p>Lorem ipsum dolor sit amet, consectetur adipiscing elit. Donec orci purus, luctus vitae dignissim eu, iaculis sed purus. Vivamus faucibus, ipsum nec aliquet viverra, leo mauris condimentum ligula, sit amet sagittis enim ligula quis arcu. Nam egestas tortor id nisi porttitor mattis. In tortor ante, ultricies in suscipit a, tempus non massa. Vivamus et auctor mi. Fusce vel massa nulla. Phasellus nec eros mauris, et scelerisque orci.</p>
      <p>Donec malesuada orci vitae nulla accumsan porta a id massa. Quisque accumsan iaculis magna sit amet fringilla. Maecenas consequat, magna eget tincidunt semper, odio nibh rutrum mi, id feugiat ante nisi eu risus. Vestibulum nunc orci, rhoncus a placerat in, ultricies in mi. Cras mattis varius eros, vel fringilla nisi suscipit eget. Quisque scelerisque sagittis nulla at porttitor.</p>
      <p>Sed id augue vitae urna euismod commodo aliquet a quam. Pellentesque arcu velit, cursus et malesuada ut, consequat et diam. Nullam erat sem, rhoncus id ullamcorper vitae, rhoncus et arcu. In ultricies ultricies nulla, ut rutrum nisi iaculis at. Donec eu magna a metus ornare faucibus. Fusce aliquet faucibus ultricies. Morbi semper, est id tincidunt gravida, sem arcu adipiscing lacus, ac bibendum nulla leo eu purus. Quisque nec diam sed risus consectetur a ccumsan quis quis nibh. Vestibulum id purus lorem.</p>
      <p>It is a long established fact that a reader will be distracted by the readable content of a page when looking at its layout. The point of using Lorem Ipsum is that it has a more-or-less normal distribution of letters, as opposed to using 'Content here, content here', making it look like readable English. Many desktop publishing packages</p>
      <div class="sign-off">Sincerely,</div>
      <span class="signature" role="img" aria-label="Handwritten signature of Daniel Hartley"></span>
    </section>

    <footer class="footer">
      <div>Level 9, 7 Ferris Lane, Sydney NSW 2000</div>
      <div>02 8472 3159 | www.qvlegal.com.au</div>
    </footer>
  </main>
</body>
</html>
```